Introduction flyer

Brightpath Dietetics & Vitality Advisory, is a new holistic nutritional therapy specialising in womens health. I want a flyer that appeals to women between 15 to 60. It must speak "health, food & balance". I have attached the basic info I need included in the text. I like Greens & Blues, soft text. My flyer will be distributed to cafes, shops, fitness centres, hung up in grocery stores & health centres etc. The QELR & HPVA logos need to appear on the flyer to show I am fully registered. My own logo & company name is attached.

Target Market(s)

Women from 10 to 60 years old.

Industry/Entity Type

Nutritionist

Colors
32a6d7
abd037
33b8a4
fbf289
ffcf3e
b768aa
d5d5d5
dcdcdc
e8e8e8

Requirements
Must have
• An image of healthy food & ladies. A group of women eating soup, stews or curry type dishes, with plenty of colour - no bread or white wine, and not just fruit please. Food that looks enjoyable to the average person.
• Nutrition is main part of my job, so please keep that in mind & emphasise food & natural well being.
Should not have
• People exercising, men, white wine, bread, cakes, sweets etc..

```html
<!DOCTYPE html>
<html lang="en">
<head>
<meta charset="utf-8">
<title>Brightpath Dietetics &amp; Vitality Advisory – Introduction Flyer</title>
<link rel="stylesheet" href="https://fonts.googleapis.com/css2?family=Cinzel:wght@700&family=Cabin:wght@400;600;700&family=Oswald:wght@500;600&family=Roboto+Condensed:wght@700&family=Dosis:wght@300&family=Open+Sans:wght@500&display=swap">
<style>
:root{
  --board:#8b5e3c;
  --lime:#abd037;
  --teal:#33b8a4;
  --sky:#32a6d7;
  --plum:#b768aa;
  --purple:#7b2a8f;
  --sun:#ffcf3e;
  --ink:#1d1d1b;
  --grey:#4a4a4a;
  --white:#ffffff;
}
*{box-sizing:border-box;margin:0;padding:0}
html,body{width:1200px;height:809px;overflow:hidden;background:var(--board)}
.canvas{position:relative;width:1200px;height:809px}
.flyer{position:absolute;top:58px;width:547px;height:707px;background:var(--white);box-shadow:3px 4px 8px rgba(0,0,0,.35);overflow:hidden}
.flyer--front{left:37px}
.flyer--back{left:610px}
.abs{position:absolute}

/* front */
.header{left:0;top:0;width:100%;height:299px;background:var(--lime);color:var(--white)}
.brand-title{left:28px;top:30px;font-family:'Cinzel',serif;font-size:25px;line-height:29px;letter-spacing:.3px;text-shadow:1px 1px 2px rgba(0,0,0,.25)}
.intro{left:28px;top:105px;font-family:'Cabin',sans-serif;font-weight:700;font-size:17px;line-height:24px;color:var(--ink)}
.services{list-style:none;font-family:'Cabin',sans-serif;font-size:10.5px;line-height:13px;color:var(--ink)}
.services li{position:relative;padding-left:20px;margin-bottom:7px}
.services li::before{content:"";position:absolute;left:2px;top:3px;width:8px;height:8px;border-radius:50%;background:var(--white)}
.services .strong{font-weight:700;font-size:13px;line-height:15px}
.services--left{left:28px;top:170px;width:260px}
.services--right{left:296px;top:168px;width:240px}
.tagline-band{left:0;top:299px;width:100%;height:32px;background:var(--plum);color:var(--white);font-family:'Roboto Condensed',sans-serif;font-size:16px;line-height:32px;padding-left:31px}
.call{left:31px;top:342px;font-family:'Cabin',sans-serif;font-weight:600;font-size:16px;color:var(--grey)}
.phone{left:31px;top:366px;font-family:'Roboto Condensed',sans-serif;font-size:29px;color:var(--purple)}
.reg{top:345px;font-family:'Cabin',sans-serif;font-weight:700;color:var(--teal)}
.reg--self{left:230px;font-size:12px;color:var(--sky);top:382px}
.reg--hpva{left:306px;top:370px;font-size:22px;color:var(--teal)}
.reg--qelr{left:406px;top:370px;font-size:24px;color:#3d2c8d;display:flex;align-items:center;gap:6px}
.reg--qelr i{display:block;width:24px;height:24px;border-radius:50%;background:var(--lime)}
.divider{top:345px;width:1px;height:64px;background:#bdbdbd}
.booking{left:0;top:422px;width:100%;height:126px;background:var(--teal);color:var(--white)}
.email{left:31px;top:8px;font-family:'Cabin',sans-serif;font-weight:600;font-size:12px;color:var(--ink)}
.book{left:31px;top:28px;font-family:'Cabin',sans-serif;font-weight:700;font-size:15px;line-height:19px;color:var(--ink)}
.fineprint{left:31px;top:72px;width:340px;font-family:'Cabin',sans-serif;font-size:7.8px;line-height:12px}
.repeat{right:31px;top:6px;text-align:right;font-family:'Cabin',sans-serif;font-weight:700;font-size:14px;line-height:19px}
.mini{right:31px;top:50px;text-align:right;font-family:'Roboto Condensed',sans-serif;font-size:25px;line-height:27px;color:var(--sun);text-shadow:1px 1px 1px rgba(0,0,0,.2)}
.food-strip{left:0;top:548px;width:100%;height:159px;display:flex;gap:3px;background:var(--teal)}
.food-strip div{flex:1}
.food--1{background:linear-gradient(160deg,#6b4c3b,#d9a06a 60%,#f0c28a)}
.food--2{background:linear-gradient(150deg,#c98a4d,#e0b060 55%,#8a5a2c)}
.food--3{background:linear-gradient(160deg,#e9e2cf,#9bbf6a 50%,#d7b45a)}
.food--4{background:linear-gradient(160deg,#d9421f,#b52a12 60%,#e9e3d6)}
.food--5{background:linear-gradient(160deg,#d93a2a,#7aa83a 55%,#4a2f25)}

/* back */
.hero{left:0;top:0;width:100%;height:331px;background:linear-gradient(120deg,#f4f1ec 0%,#e9d9c8 40%,#c8d9c0 70%,#e2ecf0 100%)}
.hero-title{left:50px;top:38px;font-family:'Open Sans',sans-serif;font-weight:500;font-size:23px;line-height:24px;color:var(--ink)}
.badge{left:426px;top:268px;width:76px;height:76px;border-radius:50%;background:var(--white);display:flex;align-items:center;justify-content:center;text-align:center;font-family:'Cabin',sans-serif;font-weight:600;font-size:12px;line-height:14px;color:var(--ink)}
.about-band{left:0;top:331px;width:100%;height:91px;background:var(--sky)}
.about{left:278px;top:341px;font-family:'Dosis',sans-serif;font-weight:300;font-size:23px;line-height:24px;color:var(--white)}
.seal{left:46px;top:258px;width:200px;height:200px;border-radius:50%;background:var(--white);border:6px solid var(--teal);display:flex;align-items:center;justify-content:center;text-align:center;font-family:'Cabin',sans-serif;font-weight:600;font-size:12px;line-height:15px;color:#1f6fa3;padding-top:40px}
.questions{left:0;top:422px;width:278px;height:285px;background:var(--lime);padding:32px 0 0 38px;font-family:'Oswald',sans-serif;font-weight:600;color:var(--ink)}
.questions p{font-size:20px;line-height:32px;letter-spacing:.3px}
.questions .lead{font-size:27px;line-height:34px;color:var(--white);margin-bottom:4px}
.questions .soft{color:var(--white)}
.questions .ask{font-size:24px;line-height:28px;color:var(--white);margin-top:10px}
.details{left:300px;top:438px;width:226px}
.details h2{font-family:'Cabin',sans-serif;font-weight:600;font-size:18.5px;line-height:22px;color:var(--plum)}
.details .body{margin-top:16px;font-family:'Cabin',sans-serif;font-size:9.4px;line-height:11.6px;color:var(--grey);text-align:justify}
.details .note{margin-top:18px;font-family:'Cabin',sans-serif;font-weight:700;font-size:12.5px;line-height:15px;color:var(--ink)}
</style>
</head>
<body>
<div class="canvas">

  <section class="flyer flyer--front">
    <div class="abs header">
      <h1 class="abs brand-title">BRIGHTPATH DIETETICS<br>&amp; VITALITY ADVISORY</h1>
      <p class="abs intro">Qualified, Registered and fully insured Nutritional<br>Therapist &amp; Wellness Consultant, specialising in:</p>
      <ul class="abs services services--left">
        <li>Fertility, IVF, pre-conception, pregnancy &amp;<br>post-natal care</li>
        <li>Menstrual cycle challenges (PCOS, Endometriosis,<br>PMS, heavy/ irregular periods etc)</li>
        <li class="strong">Thyroid conditions</li>
        <li>Low libido</li>
      </ul>
      <ul class="abs services services--right">
        <li class="strong">Digestive health</li>
        <li>Chronic fatigue syndrome</li>
        <li class="strong">Perimenopause/menopause</li>
        <li>Weight management</li>
        <li>Type 2 diabetes, blood sugar dysregulation,<br>high blood pressure, high cholesterol</li>
      </ul>
    </div>
    <div class="abs tagline-band">Small changes to your diet may lead to big changes in your health.</div>
    <p class="abs call">Call Maeve today on</p>
    <p class="abs phone">085-4427-316</p>
    <span class="abs reg reg--self">Brightpath</span>
    <span class="abs divider" style="left:293px"></span>
    <span class="abs reg reg--hpva">HPVA</span>
    <span class="abs divider" style="left:387px"></span>
    <span class="abs reg reg--qelr"><i></i>QELR</span>
    <div class="abs booking">
      <p class="abs email">or email maeve@brightpathdietetics.ie</p>
      <p class="abs book">to book a consultation or for<br>a FREE No Obligation</p>
      <p class="abs fineprint">Initial consultations typically last up to 2 hours, follow-ups 30 – 60 minutes.<br>Further investigative tests may be recommended such as blood, urine, saliva<br>sampling. These will always be agreed with the client in advance.</p>
      <p class="abs repeat">Small changes to your diet may<br>lead to big changes in your health</p>
      <p class="abs mini">15 Minute Mini<br>Consultation</p>
    </div>
    <div class="abs food-strip">
      <div class="food--1" role="img" aria-label="Smiling woman eating a bowl of soup"></div>
      <div class="food--2" role="img" aria-label="Colourful bean and vegetable stew in a wooden bowl"></div>
      <div class="food--3" role="img" aria-label="Vegetable broth with fresh herbs and onions"></div>
      <div class="food--4" role="img" aria-label="Tomato soup garnished with basil"></div>
      <div class="food--5" role="img" aria-label="Vegetable stew with peppers and tomatoes"></div>
    </div>
  </section>

  <section class="flyer flyer--back">
    <div class="abs hero" role="img" aria-label="Mother and daughter in a bright kitchen holding pepper rings to their eyes, surrounded by fresh vegetables"></div>
    <h2 class="abs hero-title">Health, Food<br>&amp; Balance</h2>
    <div class="abs badge">EAT WELL<br>LIVE WELL</div>
    <div class="abs about-band"></div>
    <p class="abs about">A New Holistic Nutritional<br>Therapy Specialising In<br>Womens Health</p>
    <div class="abs seal">Brightpath Dietetics<br>&amp; Vitality Advisory</div>
    <div class="abs questions">
      <p class="lead">DO YOU EXPERIENCE</p>
      <p>LOW ENERGY,</p>
      <p>LOW LIBIDO,</p>
      <p>MENSTRUAL CYCLE,</p>
      <p>COMPLICATIONS, <span class="soft">OR</span></p>
      <p class="ask">ARE YOU PLANNING<br>A BABY?</p>
    </div>
    <div class="abs details">
      <h2>Small changes to your diet may lead to big changes in your health.</h2>
      <p class="body">Discover exactly what YOU need to change and how to make these changes long lasting. There is no 1 rule-fits-all. My nutritional advice aims to dig up the root cause to my client's health concerns. My lifestyle plans are completely personalised to an individual's needs and circumstances. I consider the whole person not just symptoms or disease.</p>
      <p class="note">Home visits available, at no extra cost within local area; I can visit your place of work or home.</p>
    </div>
  </section>

</div>
</body>
</html>
```